Ridgeway Mining Solutions Business Card

Ridgeway Mining Solutions is a company that provides consulting services to the Mining Industry.

Whilst Ridgeway Mining Solutions is an Australian based company its client base is the global mining industry.

The essence of Ridgeway Mining Solutions is its a can do organisation that can make a difference to its clients by providing quality assistance and form lasting relationships.
Updates

Target Market(s)

The global Mining Industry.

Industry/Entity Type

Mining

Font styles to use
Serif

Colors

Designer to choose colors to be used in the design.

Requirements
Nice to have
• My thinking is the card would look good in black given the logo.

I would like to see written on the back side of the card " Providing Metallurgical, Management and Corporate Services to the Mining Industry"

```html
<!DOCTYPE html>
<html lang="en">
<head>
<meta charset="utf-8">
<title>Ridgeway Mining Solutions – Business Card</title>
<link rel="stylesheet" href="https://fonts.googleapis.com/css2?family=Tinos:wght@400;700&display=swap">
<style>
  :root {
    --amber: #f5b335;
    --ink: #3a3a3a;
    --slate: #5c5c5c;
    --paper: #ffffff;
    --night: #050505;
    --backdrop-top: #e4e4e4;
    --backdrop-bottom: #bdbdbd;
  }
  * { box-sizing: border-box; margin: 0; padding: 0; }
  html, body { width: 1200px; height: 864px; overflow: hidden; }
  body {
    background: linear-gradient(180deg, var(--backdrop-top), var(--backdrop-bottom));
    font-family: "Tinos", "Times New Roman", serif;
    display: flex;
    flex-direction: column;
    align-items: center;
    justify-content: center;
    gap: 56px;
  }
  .card {
    width: 630px;
    height: 360px;
    position: relative;
    box-shadow: 0 10px 28px rgba(0,0,0,0.25);
  }
  /* Front */
  .card-front { background: var(--paper); display: flex; align-items: center; }
  .front-brand {
    width: 300px;
    display: flex;
    align-items: center;
    justify-content: center;
    gap: 12px;
    padding-left: 20px;
  }
  .brand-mark { width: 18px; height: 18px; background: var(--amber); flex: none; }
  .brand-name {
    color: var(--amber);
    font-weight: 700;
    font-size: 30px;
    line-height: 1.05;
  }
  .divider {
    width: 2px;
    height: 250px;
    background: var(--slate);
    margin: 0 34px 0 10px;
  }
  .contact { color: var(--ink); }
  .person-name { font-size: 25px; line-height: 1; }
  .person-title { font-size: 15px; color: var(--slate); margin: 4px 0 22px 2px; }
  .contact-list { list-style: none; }
  .contact-list li {
    display: flex;
    align-items: flex-start;
    gap: 14px;
    font-size: 18px;
    line-height: 1.15;
    margin-bottom: 9px;
  }
  .contact-list svg { width: 20px; height: 18px; flex: none; margin-top: 1px; }
  /* Back */
  .card-back {
    background: var(--night);
    display: flex;
    flex-direction: column;
    align-items: center;
    justify-content: center;
    gap: 40px;
  }
  .back-brand { display: flex; align-items: center; gap: 14px; }
  .back-brand .brand-name { font-size: 38px; }
  .back-brand .brand-mark { width: 22px; height: 22px; }
  .tagline { color: var(--paper); font-size: 20px; }
</style>
</head>
<body>
  <section class="card card-front">
    <div class="front-brand">
      <span class="brand-mark"></span>
      <span class="brand-name">Ridgeway<br>Mining Solutions</span>
    </div>
    <div class="divider"></div>
    <div class="contact">
      <p class="person-name">Daniel Marsh</p>
      <p class="person-title">Managing Director</p>
      <ul class="contact-list">
        <li>
          <svg viewBox="0 0 20 18" aria-hidden="true"><path d="M2 6 Q10 0 18 6 L16 8 L13 6 L13 4 Q10 3 7 4 L7 6 L4 8 Z M5 9 H15 L17 16 H3 Z" fill="var(--amber)"/></svg>
          <span>0098 7654 321</span>
        </li>
        <li>
          <svg viewBox="0 0 20 18" aria-hidden="true"><rect x="1" y="3" width="18" height="12" fill="var(--amber)"/><path d="M1 3 L10 10 L19 3" stroke="#fff" stroke-width="1.5" fill="none"/></svg>
          <span>info@ridgewaymining.com</span>
        </li>
        <li>
          <svg viewBox="0 0 20 18" aria-hidden="true"><rect x="2" y="2" width="16" height="11" fill="none" stroke="var(--amber)" stroke-width="2"/><rect x="7" y="14" width="6" height="2" fill="var(--amber)"/></svg>
          <span>www.ridgewaymining.com</span>
        </li>
        <li>
          <svg viewBox="0 0 20 18" aria-hidden="true"><path d="M10 1 L19 9 L16 9 L16 17 L12 17 L12 12 L8 12 L8 17 L4 17 L4 9 L1 9 Z" fill="var(--amber)"/></svg>
          <span>Ridgeway Consulting Pty 000<br>Ave Perth, WA 0000</span>
        </li>
      </ul>
    </div>
  </section>

  <section class="card card-back">
    <div class="back-brand">
      <span class="brand-mark"></span>
      <span class="brand-name">Ridgeway Mining Solutions</span>
    </div>
    <p class="tagline">We provide consulting services to the Mining Industry..</p>
  </section>
</body>
</html>
```